BRW Business Card
Belrow Construction Services
BRW Business Card -
Creative Brief
Professional
Orin Belrow
2742 Quillan Street Shreveport, LA 71584
obelrow@BelrowBW.com
BelrowBW.com
Logo and contact info on front. Logo to take up most of front of card with contact info in smaller text.
Belrow Construction Services (Notes) I would like a light grey color on the back with a navy border

```html
<!DOCTYPE html>
<html lang="en">
<head>
<meta charset="utf-8">
<title>Belrow Construction Services Stationery</title>
<link href="https://fonts.googleapis.com/css2?family=Open+Sans:wght@400;700;800&display=swap" rel="stylesheet">
<style>
:root{
  --navy:#1d3a6b;
  --navy-dark:#142b52;
  --grey:#cfd3d8;
  --grey-light:#e4e7ea;
  --paper:#ffffff;
  --ink:#3a4450;
  --faint:#e6e9ec;
  --stage:#eef0f2;
}
*{box-sizing:border-box;margin:0;padding:0}
html,body{width:1200px;height:341px;overflow:hidden;background:var(--stage);font-family:"Open Sans",Arial,sans-serif;color:var(--ink)}
.canvas{position:relative;width:1200px;height:341px}
.piece{position:absolute;background:var(--paper);box-shadow:0 1px 4px rgba(0,0,0,.18);overflow:hidden}
.wordmark{font-weight:800;letter-spacing:1px;line-height:1;color:var(--navy)}
.wordmark.light{color:var(--paper)}
.tiny{font-size:4px;line-height:1.5;color:var(--ink)}
/* business cards */
.card{width:137px;height:70px;border-radius:3px}
.card-front{left:24px;top:34px}
.card-front .band{position:absolute;left:0;top:0;width:100%;height:32px;background:var(--navy)}
.card-front .logo-panel{position:absolute;left:8px;top:5px;width:56px;height:22px;background:var(--paper);display:flex;align-items:center;justify-content:center}
.card-front .logo-panel .wordmark{font-size:15px}
.card-front .contact{position:absolute;left:8px;top:38px;width:120px}
.card-front .contact .name{font-size:5px;font-weight:700;color:var(--navy)}
.card-back-grey{left:24px;top:118px;background:var(--grey-light);border:3px solid var(--navy);display:flex;align-items:center;justify-content:center;flex-direction:column}
.card-back-grey .wordmark{font-size:20px}
.card-back-grey .tag{font-size:3.5px;margin-top:3px;color:var(--navy)}
.card-back-navy{left:24px;top:230px;background:var(--navy);display:flex;align-items:center;justify-content:center}
.card-back-navy .wordmark{font-size:24px}
/* letterheads */
.letterhead{top:22px;width:226px;height:296px}
.letterhead.one{left:176px}
.letterhead.two{left:414px}
.letterhead .band{position:absolute;left:0;top:0;width:100%;height:22px;background:var(--navy)}
.letterhead .logo-panel{position:absolute;left:82px;top:3px;width:62px;height:18px;background:var(--paper);display:flex;align-items:center;justify-content:center}
.letterhead.one .logo-panel{left:10px}
.letterhead .logo-panel .wordmark{font-size:13px}
.letterhead .head-contact{position:absolute;right:10px;top:6px;color:#fff;font-size:3.5px;line-height:1.5;text-align:right}
.letterhead .rule{position:absolute;left:10px;right:10px;top:28px;height:1px;background:var(--grey)}
.letterhead .ghost{position:absolute;left:0;right:0;top:118px;text-align:center;font-size:52px;font-weight:800;color:var(--faint);letter-spacing:2px}
.letterhead .foot{position:absolute;left:0;right:0;bottom:8px;text-align:center;font-size:3.5px;color:var(--ink)}
/* small envelopes */
.env-small{left:646px;width:182px;height:104px}
.env-small.one{top:66px}
.env-small.two{top:204px}
.env-small .band{position:absolute;left:0;top:0;width:100%;height:14px;background:var(--navy)}
.env-small .logo-panel{position:absolute;left:8px;top:3px;width:44px;height:13px;background:var(--paper);display:flex;align-items:center;justify-content:center}
.env-small .logo-panel .wordmark{font-size:9px}
.env-small .ghost{position:absolute;right:16px;top:46px;font-size:30px;font-weight:800;color:var(--faint)}
.env-small .return{position:absolute;left:8px;top:20px}
/* long envelopes */
.env-long{left:846px;width:306px;height:78px}
.env-long svg{position:absolute;inset:0}
.env-long.a{top:42px}
.env-long.b{top:132px}
.env-long.c{top:222px}
.env-long .addr{position:absolute;left:120px;top:40px;font-size:4px;color:var(--ink)}
</style>
</head>
<body>
<main class="canvas">

  <section class="piece card card-front" aria-label="Business card front">
    <div class="band"></div>
    <div class="logo-panel"><span class="wordmark">BRW</span></div>
    <div class="contact tiny">
      <p class="name">Orin Belrow</p>
      <p>2742 Quillan Street Shreveport, LA 71584</p>
      <p>obelrow@BelrowBW.com · BelrowBW.com</p>
      <p>Office 318 555 0142 · Cell 318 555 0187</p>
    </div>
  </section>

  <section class="piece card card-back-grey" aria-label="Business card back, grey">
    <span class="wordmark">BRW</span>
    <span class="tag">Belrow Construction Services</span>
  </section>

  <section class="piece card card-back-navy" aria-label="Business card back, navy">
    <span class="wordmark light">BRW</span>
  </section>

  <section class="piece letterhead one" aria-label="Letterhead">
    <div class="band"></div>
    <div class="logo-panel"><span class="wordmark">BRW</span></div>
    <div class="head-contact"><p>2742 Quillan Street</p><p>Shreveport, LA 71584</p><p>318 555 0142</p></div>
    <div class="rule"></div>
    <div class="ghost">BRW</div>
    <p class="foot">BelrowBW.com</p>
  </section>

  <section class="piece letterhead two" aria-label="Letterhead, second page">
    <div class="band"></div>
    <div class="logo-panel"><span class="wordmark">BRW</span></div>
    <div class="ghost">BRW</div>
    <p class="foot">2742 Quillan Street Shreveport, LA 71584 · BelrowBW.com</p>
  </section>

  <section class="piece env-small one" aria-label="Envelope front">
    <div class="band"></div>
    <div class="logo-panel"><span class="wordmark">BRW</span></div>
    <div class="return tiny"><p>2742 Quillan Street</p><p>Shreveport, LA 71584</p></div>
    <div class="ghost">BRW</div>
  </section>

  <section class="piece env-small two" aria-label="Envelope front, alternate">
    <div class="band"></div>
    <div class="logo-panel"><span class="wordmark">BRW</span></div>
    <div class="return tiny"><p>2742 Quillan Street</p><p>Shreveport, LA 71584</p></div>
    <div class="ghost">BRW</div>
  </section>

  <section class="piece env-long a" aria-label="Envelope back with navy flap">
    <svg viewBox="0 0 306 78" aria-hidden="true">
      <rect width="306" height="78" fill="var(--grey-light)"/>
      <path d="M0 0H306V14Q153 46 0 14Z" fill="var(--navy)"/>
    </svg>
    <p class="addr">BelrowBW.com</p>
  </section>

  <section class="piece env-long b" aria-label="Envelope back">
    <svg viewBox="0 0 306 78" aria-hidden="true">
      <rect width="306" height="78" fill="var(--paper)"/>
      <path d="M0 0H306V12Q153 40 0 12Z" fill="var(--navy)"/>
      <path d="M0 78L140 42Q153 38 166 42L306 78" fill="none" stroke="var(--grey)" stroke-width="1"/>
    </svg>
  </section>

  <section class="piece env-long c" aria-label="Envelope back, white">
    <svg viewBox="0 0 306 78" aria-hidden="true">
      <rect width="306" height="78" fill="var(--paper)"/>
      <path d="M0 0L140 44Q153 48 166 44L306 0" fill="none" stroke="var(--grey)" stroke-width="1"/>
      <path d="M0 78L120 40M306 78L186 40" fill="none" stroke="var(--grey)" stroke-width="1"/>
    </svg>
  </section>

</main>
</body>
</html>
```